TA BRAMLEY BUSINESS CARD DESIGN PROJECT

We need to utilize our logo that was expertly created on PixelHarbor and now need to match this with a business card design.

```html
<!DOCTYPE html>
<html lang="en">
<head>
<meta charset="utf-8">
<title>TA Bramley Business Card</title>
<link href="https://fonts.googleapis.com/css2?family=Lato:wght@400;700;900&display=swap" rel="stylesheet">
<style>
  :root {
    --brand-blue: #0452a8;
    --card-white: #ffffff;
    --ink: #2b2b2b;
    --backdrop: #3a3a3a;
  }
  * { margin: 0; padding: 0; box-sizing: border-box; }
  html, body { width: 1200px; height: 875px; overflow: hidden; }
  body {
    background: var(--backdrop);
    font-family: "Lato", sans-serif;
    position: relative;
  }
  .card {
    position: absolute;
    top: 282px;
    width: 540px;
    height: 310px;
    border-radius: 18px;
    overflow: hidden;
  }
  .card-front { left: 40px; background: var(--brand-blue); }
  .card-back { left: 620px; background: var(--card-white); }

  .wordmark {
    font-family: "Lato", sans-serif;
    font-weight: 900;
    text-transform: uppercase;
    letter-spacing: 0.18em;
    white-space: nowrap;
  }
  .card-front .wordmark {
    position: absolute;
    left: 0; right: 0; top: 132px;
    text-align: center;
    font-size: 44px;
    color: #dfe3e8;
  }
  .card-back .wordmark {
    position: absolute;
    left: 36px; top: 70px;
    font-size: 30px;
    color: var(--brand-blue);
  }

  .contact-list {
    position: absolute;
    left: 38px; top: 150px;
    list-style: none;
    font-size: 13px;
    line-height: 1.55;
    color: var(--ink);
  }
  .contact-list li { display: flex; align-items: flex-start; gap: 9px; }
  .contact-list svg { width: 11px; height: 11px; margin-top: 4px; flex: none; fill: var(--brand-blue); }

  .name-band {
    position: absolute;
    right: 0; top: 92px;
    width: 250px; height: 80px;
    background: var(--brand-blue);
    clip-path: polygon(14% 0, 100% 0, 100% 100%, 0 100%);
    color: var(--card-white);
    text-align: right;
    padding: 16px 22px 0 0;
  }
  .name-band .person-name {
    font-size: 21px; font-weight: 700; letter-spacing: 0.02em; text-transform: uppercase;
  }
  .name-band .person-role { font-size: 14px; font-weight: 400; margin-top: 2px; }
</style>
</head>
<body>
  <section class="card card-front">
    <div class="wordmark">TA Bramley</div>
  </section>

  <section class="card card-back">
    <div class="wordmark">TA Bramley</div>

    <ul class="contact-list">
      <li>
        <svg viewBox="0 0 12 12"><path d="M6 0a4 4 0 0 0-4 4c0 3 4 8 4 8s4-5 4-8a4 4 0 0 0-4-4zm0 5.6A1.6 1.6 0 1 1 6 2.4a1.6 1.6 0 0 1 0 3.2z"/></svg>
        <span>123 Anywhere St.<br>Any City, ST 12345</span>
      </li>
      <li>
        <svg viewBox="0 0 12 12"><path d="M2.4 0.6l2 2.2-1 1.4a7 7 0 0 0 4.4 4.4l1.4-1 2.2 2-1.2 1.8C5 11.2 0.8 7 0.6 1.8z"/></svg>
        <span>(123) 456-7890</span>
      </li>
      <li>
        <svg viewBox="0 0 12 12"><path d="M3 0h6a1 1 0 0 1 1 1v10a1 1 0 0 1-1 1H3a1 1 0 0 1-1-1V1a1 1 0 0 1 1-1zm0.6 1.4v7.6h4.8V1.4z"/></svg>
        <span>(231) 456-7890</span>
      </li>
      <li>
        <svg viewBox="0 0 12 12"><path d="M0 2h12v8H0zm1 1 5 3.6L11 3z"/></svg>
        <span>hello@website.com</span>
      </li>
      <li>
        <svg viewBox="0 0 12 12"><circle cx="6" cy="6" r="5.5"/><path d="M0.5 6h11M6 0.5c-2.4 2.6-2.4 8.4 0 11M6 0.5c2.4 2.6 2.4 8.4 0 11" stroke="#fff" stroke-width="0.8" fill="none"/></svg>
        <span>www.website.com</span>
      </li>
    </ul>

    <div class="name-band">
      <div class="person-name">Owen Calder</div>
      <div class="person-role">Founder &amp; CEO</div>
    </div>
  </section>
</body>
</html>
```